Business Card Design needed - Something Awesome!

Need a business card designed. Company is "Marlowe Advisory" we do consulting and also have sales automation technology.
I'm going to use thick stock or metal, something really nice... I was thinking about a QR Code on the back that would just upload my contact info to the persons contact, etc -

This is a Strategy Company with a tech feel. I'm open to ideas but really want this to be nice!

I need a template that should include:

Name | Position or Title
D: 415.902.3376
www.marloweadvisory.example

I'm going to attach my contact so you can use that one, I need to get this printed.

Target Market(s)

Small to mid size customers, Entrepreneurs etc.

Industry/Entity Type

Consulting, Tech, Private Equity.

Contact Information for Business Card

Name, Phone, Maybe email, URL

Font styles to use
Sans Serif

Colors

Designer to choose only greyscale colors for use in the design.

Requirements
Must have
• Fresh, Clean, stand out from the crowd - will be on thick stock or metal.
Nice to have
• Clean, simple yet impactful.
Should not have
• Not cartoonish

```html
<!DOCTYPE html>
<html lang="en">
<head>
<meta charset="utf-8">
<title>Marlowe Advisory — Business Card</title>
<link rel="stylesheet" href="https://fonts.googleapis.com/css2?family=Roboto:wght@300;400;700&display=swap">
<style>
  :root {
    --backdrop: #2f2f2f;
    --card: #161616;
    --card-edge: #0c0c0c;
    --silver: #cfcfcf;
    --silver-soft: #a9a9a9;
    --divider: #5a5a5a;
    --pattern-dark: #0d0d0d;
    --pattern-mid: #2a2a2a;
    --pattern-light: #4a4a4a;
  }
  * { margin: 0; padding: 0; box-sizing: border-box; }
  html, body {
    width: 1200px;
    height: 801px;
    overflow: hidden;
    background: var(--backdrop);
    font-family: "Roboto", Arial, sans-serif;
  }
  .sheet {
    width: 1200px;
    height: 801px;
    display: flex;
    align-items: center;
    justify-content: center;
    gap: 40px;
  }
  .card {
    position: relative;
    width: 540px;
    height: 309px;
    background: var(--card);
    border: 1px solid var(--card-edge);
    box-shadow: 0 14px 30px rgba(0,0,0,0.35);
    overflow: hidden;
  }

  /* Front */
  .card-front .wordmark {
    position: absolute;
    left: 44px;
    top: 70px;
    font-size: 62px;
    font-weight: 400;
    letter-spacing: 4px;
    color: var(--silver);
    line-height: 1;
  }
  .card-front .details {
    position: absolute;
    left: 44px;
    right: 30px;
    bottom: 46px;
    display: flex;
    align-items: stretch;
  }
  .identity {
    padding-right: 20px;
    border-right: 1px solid var(--divider);
    display: flex;
    flex-direction: column;
    justify-content: flex-end;
  }
  .identity .person-name {
    font-size: 19px;
    font-weight: 700;
    color: var(--silver);
    letter-spacing: 0.5px;
    white-space: nowrap;
  }
  .identity .person-title {
    font-size: 15px;
    font-weight: 300;
    color: var(--silver-soft);
    text-align: right;
    margin-top: 2px;
  }
  .contacts {
    list-style: none;
    padding-left: 18px;
    display: flex;
    flex-direction: column;
    gap: 4px;
  }
  .contacts li {
    display: flex;
    align-items: center;
    gap: 7px;
    font-size: 13.5px;
    font-weight: 300;
    color: var(--silver);
    white-space: nowrap;
  }
  .contacts svg { width: 11px; height: 11px; flex: none; }

  /* Back */
  .card-back .pattern-field {
    position: absolute;
    inset: 0;
    background: linear-gradient(120deg, var(--pattern-dark) 0%, var(--pattern-mid) 55%, var(--pattern-light) 100%);
  }
  .card-back .back-name {
    position: absolute;
    left: 0;
    right: 0;
    top: 50%;
    transform: translateY(-50%);
    text-align: center;
    font-size: 22px;
    font-weight: 400;
    letter-spacing: 4px;
    color: var(--silver);
  }
</style>
</head>
<body>
<main class="sheet">
  <section class="card card-front" aria-label="Card front">
    <div class="wordmark">MARLOWE</div>
    <div class="details">
      <div class="identity">
        <div class="person-name">JULIAN R. HALE</div>
        <div class="person-title">Founder / CEO</div>
      </div>
      <ul class="contacts">
        <li>
          <svg viewBox="0 0 12 12" aria-hidden="true"><circle cx="6" cy="6" r="6" fill="#cfcfcf"/><path d="M4 3.2l1 1.4-.6.7c.4.9 1.1 1.6 2 2l.7-.6 1.4 1-.6 1c-2.4-.3-4.4-2.3-4.6-4.7z" fill="#161616"/></svg>
          415.902.3376
        </li>
        <li>
          <svg viewBox="0 0 12 12" aria-hidden="true"><rect x="1" y="2.5" width="10" height="7" fill="#cfcfcf"/><path d="M1 2.5l5 4 5-4" fill="none" stroke="#161616" stroke-width="1"/></svg>
          info@marloweadvisory.example
        </li>
        <li>
          <svg viewBox="0 0 12 12" aria-hidden="true"><circle cx="6" cy="6" r="5.5" fill="#cfcfcf"/><path d="M0.5 6h11M6 .5c-2.5 3-2.5 8 0 11M6 .5c2.5 3 2.5 8 0 11" fill="none" stroke="#161616" stroke-width=".8"/></svg>
          www.marloweadvisory.example
        </li>
      </ul>
    </div>
  </section>

  <section class="card card-back" aria-label="Card back">
    <div class="pattern-field" role="img" aria-label="Diagonal pattern of glossy black and grey squares"></div>
    <div class="back-name">MARLOWE</div>
  </section>
</main>
</body>
</html>
```